Larkspur Talent IT Recruiting firm needs a business card design for Recruiters, Sourcers, and Account

We need business cards that allow us to change all contact info, names, titles (Recruiter, Sourcer, Account Manager, Director, CEO, etc) per person since we have three offices, in three cities, Phoenix, Austin, and Las Vegas. We do recruiting and contractors for IT positions (Developers, Architects, Software Engineers, Security Engineers, Help Desk, DBAs, PMs, Scrum Masters, etc.) Our client companies are very diverse from Meridian 100 to silicone Valley type start-ups.

So, while we what hip, techie, and quirky, it still needs to be professional. Primary color we use is blue, with silver as a secondary color.

Target Market(s)

IT, Technology

Industry/Entity Type

Business

Contact Information for Business Card

Company name: Larkspur Talent, Inc.
Website: www.larkspurtalent.example
Logos for Careerloop, Blipster, and Myriada

Name, Title, Office Number, Cell Number, email

Font styles to use
Serif
Sans Serif

Colors
0455a3
d5d5d5

Requirements
Nice to have
• The grey I selected below is not necessary - but, would like silver included. I included a card design (File 3: LTI early trial example.jpg) that I had started on. It's very rough, and not quite what we're looking for, but what we did like is the logo, big, maybe a bit faded, off center, goes out of frame, etc. Still looking for other ideas - you are the pros! But, just an idea of a design element we liked.

```html
<!DOCTYPE html>
<html lang="en">
<head>
<meta charset="utf-8">
<title>Larkspur Talent – Business Card</title>
<link rel="stylesheet" href="https://fonts.googleapis.com/css2?family=Marcellus&family=Belleza&family=Open+Sans:wght@400&display=swap">
<style>
  :root {
    --stage: #1c1c1c;
    --brand-blue: #0455a3;
    --brand-blue-light: #1b8fd9;
    --ink: #222222;
    --paper: #ffffff;
    --card-grey: #555555;
    --card-grey-light: #5f5f5f;
    --strip-grey: #5a5a5a;
    --silver: #d5d5d5;
    --silver-soft: rgba(213, 213, 213, 0.14);
    --white: #ffffff;
  }
  * { box-sizing: border-box; margin: 0; padding: 0; }
  html, body { width: 1200px; height: 907px; overflow: hidden; }
  body { background: var(--stage); position: relative; }

  .card {
    position: absolute;
    left: 300px;
    width: 600px;
    height: 343px;
    overflow: hidden;
  }

  /* Front */
  .card-front { top: 98px; background: var(--paper); }
  .card-front .top-band {
    position: absolute; left: 0; top: 0; width: 100%; height: 13px;
    background: linear-gradient(90deg, var(--brand-blue), var(--brand-blue-light) 50%, var(--brand-blue));
  }
  .card-front .bottom-strip {
    position: absolute; left: 0; bottom: 0; width: 100%; height: 12px;
    background: var(--strip-grey);
  }
  .brand-lockup {
    position: absolute; left: 0; right: 0; top: 128px;
    text-align: center;
  }
  .brand-name {
    font-family: "Marcellus", serif;
    font-size: 34px; letter-spacing: 3px; line-height: 1;
    color: var(--ink);
    text-transform: uppercase;
  }
  .brand-tagline {
    margin-top: 16px;
    font-family: "Marcellus", serif;
    font-size: 15px; letter-spacing: 2px;
    color: var(--ink);
    text-transform: uppercase;
  }

  /* Back */
  .card-back {
    top: 475px;
    background: linear-gradient(180deg, var(--card-grey), var(--card-grey-light));
  }
  .brand-watermark {
    position: absolute; left: 225px; top: -20px; width: 420px; height: 380px;
    background: radial-gradient(ellipse at 60% 45%, var(--silver-soft), rgba(213,213,213,0.05) 60%, transparent 75%);
  }
  .holder-name {
    position: absolute; left: 32px; top: 28px;
    font-family: "Belleza", sans-serif;
    font-size: 28px; color: var(--white);
  }
  .holder-title {
    position: absolute; left: 32px; top: 67px;
    font-family: "Belleza", sans-serif;
    font-size: 19px; color: var(--white);
  }
  .contact-list {
    position: absolute; left: 32px; top: 224px;
    list-style: none;
    font-family: "Open Sans", sans-serif;
    font-size: 15px; color: var(--white);
  }
  .contact-list li {
    display: flex; align-items: center; gap: 12px;
    height: 23px;
  }
  .contact-list svg { width: 14px; height: 14px; fill: var(--white); flex: none; }
  .social-list {
    position: absolute; right: 40px; top: 283px;
    display: flex; gap: 10px; list-style: none;
    font-family: "Open Sans", sans-serif;
    font-size: 12px; color: var(--white);
  }
  .social-list li { display: flex; align-items: center; gap: 5px; }
  .social-list .social-square {
    width: 12px; height: 12px; background: var(--brand-blue-light); border-radius: 2px;
  }
</style>
</head>
<body>

<section class="card card-front" aria-label="Card front">
  <div class="top-band"></div>
  <div class="brand-lockup">
    <div class="brand-name">Larkspur Talent</div>
    <div class="brand-tagline">Connecting Tech to Teams</div>
  </div>
  <div class="bottom-strip"></div>
</section>

<section class="card card-back" aria-label="Card back">
  <div class="brand-watermark" role="img" aria-label="Large faded brand emblem running off the edge"></div>
  <div class="holder-name">Dana Whitlock</div>
  <div class="holder-title">Manager</div>

  <ul class="contact-list">
    <li>
      <svg viewBox="0 0 16 16" aria-hidden="true"><path d="M3 1c1 0 2 2.5 2 3.5S3.8 6 4.3 7.5 7 11 8.5 11.5 10 10.5 11 10.8s3.7 1.4 3.7 2.4-1.5 2.3-2.8 2.3C6.5 15.5.5 9.6.5 4 .5 2.5 2 1 3 1z"/></svg>
      555-014-2270
    </li>
    <li>
      <svg viewBox="0 0 16 16" aria-hidden="true"><path d="M4.5 0h7a1 1 0 0 1 1 1v14a1 1 0 0 1-1 1h-7a1 1 0 0 1-1-1V1a1 1 0 0 1 1-1zm1 2v5h5V2zm0 7v1.5h1.5V9zm2.5 0v1.5h1.5V9zm-2.5 2.5V13h1.5v-1.5zm2.5 0V13h1.5v-1.5z"/></svg>
      555-019-6631
    </li>
    <li>
      <svg viewBox="0 0 16 16" aria-hidden="true"><path d="M1 3h14v10H1zm1.5 1.2v.4L8 9l5.5-4.4v-.4zm0 2.3v5.3h11V6.5L8 10.8z"/></svg>
      info@larkspurtalent.example
    </li>
    <li>
      <svg viewBox="0 0 16 16" aria-hidden="true"><path d="M8 1a7 7 0 1 0 0 14A7 7 0 0 0 8 1zm0 1.2c.8.6 1.5 2 1.8 3.8H6.2C6.5 4.2 7.2 2.8 8 2.2zM2.3 7.2h2.8a13 13 0 0 0 0 1.6H2.3a5.8 5.8 0 0 1 0-1.6zm4 0h3.4a12 12 0 0 1 0 1.6H6.3a12 12 0 0 1 0-1.6zm4.6 0h2.8a5.8 5.8 0 0 1 0 1.6h-2.8a13 13 0 0 0 0-1.6zM6.2 10h3.6c-.3 1.8-1 3.2-1.8 3.8-.8-.6-1.5-2-1.8-3.8z"/></svg>
      www.larkspurtalent.example
    </li>
  </ul>

  <ul class="social-list">
    <li><span class="social-square"></span>Careerloop</li>
    <li><span class="social-square"></span>Blipster</li>
    <li><span class="social-square"></span>Myriada</li>
  </ul>
</section>

</body>
</html>
```